Package design for a set of baby wood brush

It has to be different from the competitions - here are the competitions, the box is the same size and shape, but I want the design to be different then others and stick out, yet to be suitable as baby product and baby shower gift.
I am going to call it "soft little crown" it will be printed on the brush itself.
1) https://www.shopvelmora.com/PIPLItot-Newborns-Toddlers-Bristles-Registry/dp/Q72KEM3R8T/ref=sr_1_7_a_it?ie=UTF8&qid=1496863496&sr=8-7&keywords=baby+brush
2) https://www.shopvelmora.com/Newborns-Toddlers-Natural-Bristles-Registry/dp/Q72TNHFDZZ/ref=sr_1_17_a_it?ie=UTF8&qid=1496863576&sr=8-17&keywords=baby+brush
3) https://www.shopvelmora.com/TotMerva-Silicone-Newborns-Toddlers-Bristles/dp/Q59RC4K83N/ref=sr_1_21_a_it?ie=UTF8&qid=1496944927&sr=8-21&keywords=baby+wood+brush
The desighn should be different then the competitors but still transmit a natural baby product. there will also be a little text and a naturlality symbols.
Thanks
Baby

```html
<!DOCTYPE html>
<html lang="en">
<head>
<meta charset="utf-8">
<title>Soft Little Crown – Baby Wooden Hair Brush Set Packaging</title>
<link rel="stylesheet" href="https://fonts.googleapis.com/css2?family=Lora:ital,wght@1,700&family=Open+Sans:ital,wght@0,400;0,600;0,700;1,600&display=swap">
<style>
  :root {
    --kraft: #d9b98c;
    --kraft-side: #cfae80;
    --maroon: #8b2b1c;
    --ink: #5b3f2c;
    --accent: #c2306c;
    --ring-a: #f7c0d4;
    --ring-b: #bfe3ef;
    --ring-c: #fbe3a0;
    --bg: #ffffff;
  }
  * { box-sizing: border-box; margin: 0; padding: 0; }
  html, body { width: 1200px; height: 982px; overflow: hidden; background: var(--bg); }
  .canvas { position: relative; width: 1200px; height: 982px; }

  .panel {
    position: absolute; top: 160px; height: 640px;
    background: var(--kraft);
    color: var(--ink);
    font-family: "Open Sans", sans-serif;
    overflow: hidden;
  }

  /* side panels */
  .spine { background: var(--kraft-side); width: 52px; }
  .spine--left { left: 228px; }
  .spine--right { left: 970px; }
  .spine-text {
    position: absolute; top: 24px; right: 8px;
    writing-mode: vertical-rl;
    height: 340px;
    font-size: 9px; line-height: 13px; color: var(--ink);
  }
  .spine--left .spine-text { transform: rotate(180deg); top: auto; bottom: 24px; right: auto; left: 8px; height: 420px; }
  .seal-list { position: absolute; left: 8px; top: 420px; display: flex; flex-direction: column; gap: 14px; }
  .seal { width: 36px; height: 36px; border-radius: 50%; background: #fff; border: 2px solid var(--maroon); }

  /* front & back */
  .front { left: 280px; width: 330px; text-align: center; }
  .back  { left: 640px; width: 330px; text-align: center; }

  .brand { margin-top: 62px; font-weight: 700; font-size: 26px; color: var(--accent); }
  .brand-tag { font-size: 11px; color: var(--ink); margin-top: 2px; }

  .ring { position: relative; width: 250px; height: 250px; margin: 22px auto 0; }
  .ring-art { display: block; }
  .product-name { font-family: "Open Sans", sans-serif; font-weight: 700; color: var(--accent); line-height: 1.1; }
  .front-name {
    position: absolute; inset: 0;
    display: flex; align-items: center; justify-content: center;
    font-size: 26px;
  }

  .headline {
    font-family: "Lora", serif; font-style: italic; font-weight: 700;
    color: var(--maroon); font-size: 19px; line-height: 23px;
  }
  .front .headline { margin-top: 40px; }
  .contents { margin-top: 34px; font-size: 12.5px; font-style: italic; font-weight: 600; color: var(--ink); line-height: 17px; }
  .contents .plus { display: block; font-style: normal; }

  .icon-band { display: block; margin: 0 auto; }
  .back .icon-band--top { margin-top: 30px; }
  .back-name { margin-top: 44px; font-size: 28px; }
  .back .headline { margin-top: 30px; }
  .copy { margin: 22px 34px 0; font-size: 11px; line-height: 15px; }
  .copy p + p { margin-top: 10px; }
  .bonus { margin-top: 12px; font-size: 11px; font-weight: 700; color: var(--maroon); text-decoration: underline; }
  .bonus-copy { margin: 2px 20px 0; font-size: 11px; line-height: 15px; }
  .bonus-copy strong { font-weight: 700; }
  .back .icon-band--bottom { margin-top: 22px; }
</style>
</head>
<body>
<main class="canvas">

  <section class="panel spine spine--left" aria-label="Left side panel">
    <p class="spine-text">Crafted by a small family team caring for little ones. Learn more at www.nolabeebaby.com</p>
  </section>

  <section class="panel front" aria-label="Front panel">
    <div class="brand">Nolabee</div>
    <div class="brand-tag">Gentle things for little ones</div>

    <div class="ring">
      <svg class="ring-art" width="250" height="250" viewBox="0 0 250 250" role="img" aria-label="Ring of colourful baby icons around the product name">
        <defs>
          <radialGradient id="ringTone" cx="50%" cy="50%" r="50%">
            <stop offset="60%" stop-color="#bfe3ef"/>
            <stop offset="80%" stop-color="#f7c0d4"/>
            <stop offset="100%" stop-color="#fbe3a0"/>
          </radialGradient>
        </defs>
        <circle cx="125" cy="125" r="122" fill="url(#ringTone)" opacity="0.85"/>
        <circle cx="125" cy="125" r="84" fill="#ffffff"/>
      </svg>
      <div class="product-name front-name">Soft Little<br>Crown</div>
    </div>

    <h1 class="headline">Baby Wooden Hair Brush Set<br>Natural Eco Friendly<br>3 Piece Set</h1>
    <p class="contents">
      Soft Hairbrush made with 100% goat hair bristles
      <span class="plus">+</span>
      Massage Hairbrush made with wooden Bristles
      <span class="plus">+</span>
      Premium wooden comb
    </p>
  </section>

  <section class="panel back" aria-label="Back panel">
    <svg class="icon-band icon-band--top" width="300" height="34" viewBox="0 0 300 34" role="img" aria-label="Band of small colourful baby icons">
      <rect x="0" y="4" width="300" height="22" rx="4" fill="#f7c0d4" opacity="0.6"/>
      <rect x="0" y="28" width="300" height="4" fill="#bfe3ef"/>
    </svg>

    <div class="product-name back-name">Soft Little Crown</div>

    <h2 class="headline">Baby Wooden Hair Brush Set<br>Natural Eco Friendly<br>3 Piece Set</h2>

    <div class="copy">
      <p>The silky soft hair bristles are gentle for the sensitive scalps of newborn and toddlers.</p>
      <p>All natural beech wood bristles stimulate the scalp and increase circulation while relaxing your baby.</p>
      <p>100% goat hair and wooden bristles condition baby's hair and evenly distributes natural oils down the shaft.</p>
      <p>Premium wooden comb perfect for sectioning hair and great for cradle cap.</p>
    </div>
    <div class="bonus">Bonus Inside</div>
    <p class="bonus-copy">Baby Nail File. Made from tempered Czech glass of the finest quality with smooth rounded ends. <strong>especially suitable for your baby.</strong></p>

    <svg class="icon-band icon-band--bottom" width="300" height="34" viewBox="0 0 300 34" role="img" aria-label="Band of small colourful baby icons">
      <rect x="0" y="2" width="300" height="4" fill="#bfe3ef"/>
      <rect x="0" y="8" width="300" height="22" rx="4" fill="#f7c0d4" opacity="0.6"/>
    </svg>
  </section>

  <section class="panel spine spine--right" aria-label="Right side panel">
    <p class="spine-text">Made of eco friendly solid beech wood. All natural, no harsh glues. Safe to clean, will not crack.</p>
    <div class="seal-list" aria-label="Natural product symbols">
      <span class="seal"></span>
      <span class="seal"></span>
      <span class="seal"></span>
    </div>
  </section>

</main>
</body>
</html>
```